Business Cards for a law firm

Business cards for our law firm. Use our silhoette logo and OAK PARTNERS - check our website (www.oakpartners.example)

Contact Information for Business Card

our silhouette logo, OAK PARTNERS, 800-555-0147, Dorian Pemberton, dorian@oakpartners.example

Requirements
Must have
• our silhouette logo, OAK PARTNERS, 800-555-0147, Dorian Pemberton, dorian@oakpartners.example

```html
<!DOCTYPE html>
<html lang="en">
<head>
<meta charset="utf-8">
<title>Oak Partners — Business Card</title>
<link rel="stylesheet" href="https://fonts.googleapis.com/css2?family=Montserrat:wght@400;700&display=swap">
<style>
  :root {
    --backdrop: #dfe4e6;
    --card-navy: #23336b;
    --ink-white: #ffffff;
    --accent-blue: #3a78c2;
    --mark-dim: #2e4f96;
    --font-main: "Montserrat", "Helvetica Neue", Arial, sans-serif;
  }
  * { margin: 0; padding: 0; box-sizing: border-box; }
  html, body {
    width: 1200px;
    height: 960px;
    overflow: hidden;
    background: var(--backdrop);
    font-family: var(--font-main);
  }
  .canvas {
    position: relative;
    width: 1200px;
    height: 960px;
  }
  .card {
    position: absolute;
    background: var(--card-navy);
    color: var(--ink-white);
  }
  .card--front {
    left: 246px;
    top: 58px;
    width: 709px;
    height: 405px;
  }
  .card--back {
    left: 249px;
    top: 500px;
    width: 702px;
    height: 401px;
  }

  /* Front: logo lockup */
  .front-mark {
    position: absolute;
    left: 112px;
    top: 150px;
    width: 92px;
    height: 92px;
    background: var(--ink-white);
  }
  .front-wordmark {
    position: absolute;
    left: 226px;
    top: 140px;
    font-weight: 400;
    font-size: 56px;
    line-height: 48px;
    letter-spacing: 2px;
    color: var(--ink-white);
    white-space: nowrap;
  }
  .front-wordmark span { display: block; }

  /* Back: vertical firm name and mark */
  .side-wordmark {
    position: absolute;
    left: 51px;
    top: 170px;
    transform: translate(-50%, -50%) rotate(-90deg);
    white-space: nowrap;
    font-weight: 400;
    font-size: 34px;
    letter-spacing: 2px;
    color: var(--accent-blue);
  }
  .side-mark {
    position: absolute;
    left: 34px;
    top: 330px;
    width: 46px;
    height: 46px;
    background: var(--mark-dim);
  }

  /* Back: person */
  .holder-name {
    position: absolute;
    right: 31px;
    top: 226px;
    font-size: 30px;
    letter-spacing: 2px;
    white-space: nowrap;
  }
  .holder-name .first { font-weight: 700; }
  .holder-name .last { font-weight: 400; }

  .contact-list {
    position: absolute;
    right: 28px;
    top: 298px;
    list-style: none;
  }
  .contact-item {
    display: flex;
    justify-content: flex-end;
    align-items: center;
    height: 22.5px;
    font-weight: 400;
    font-size: 14.5px;
    letter-spacing: 1px;
    white-space: nowrap;
  }
  .contact-item--phone { font-size: 19px; letter-spacing: 0.6px; }
  .contact-icon {
    width: 16px;
    height: 16px;
    margin-left: 14px;
    flex: none;
  }
</style>
</head>
<body>
<main class="canvas">

  <section class="card card--front" aria-label="Card front">
    <div class="front-mark" role="img" aria-label="Firm logo mark"></div>
    <h1 class="front-wordmark"><span>OAK</span><span>PARTNERS</span></h1>
  </section>

  <section class="card card--back" aria-label="Card back">
    <div class="side-wordmark">OAK PARTNERS</div>
    <div class="side-mark" role="img" aria-label="Firm logo mark"></div>

    <h2 class="holder-name"><span class="first">DORIAN</span> <span class="last">PEMBERTON</span></h2>

    <ul class="contact-list">
      <li class="contact-item contact-item--phone">800-555-0147
        <svg class="contact-icon" viewBox="0 0 16 16" aria-hidden="true">
          <path d="M3.2 1.5 5.4 1l1.3 3-1.5 1.2c.8 1.9 2.1 3.3 4 4.2l1.3-1.5 3 1.3-.5 2.3c-.2.7-.8 1.1-1.5 1C6.2 12 2.7 8.4 2.2 3c0-.7.4-1.3 1-1.5Z" fill="#fff"/>
          <path d="M9.5 2.2a4.5 4.5 0 0 1 4.3 4.3M9.3 4.3a2.4 2.4 0 0 1 2.4 2.4" stroke="#fff" stroke-width="1.1" fill="none" stroke-linecap="round"/>
        </svg>
      </li>
      <li class="contact-item">WWW.OAKPARTNERS.EXAMPLE
        <svg class="contact-icon" viewBox="0 0 16 16" aria-hidden="true">
          <circle cx="8" cy="8" r="6.8" fill="none" stroke="#fff" stroke-width="1.4"/>
          <ellipse cx="8" cy="8" rx="3" ry="6.8" fill="none" stroke="#fff" stroke-width="1.1"/>
          <path d="M1.5 8h13M2.5 4.8h11M2.5 11.2h11" stroke="#fff" stroke-width="1.1"/>
        </svg>
      </li>
      <li class="contact-item">DORIAN@OAKPARTNERS.EXAMPLE
        <svg class="contact-icon" viewBox="0 0 16 16" aria-hidden="true">
          <path d="M1.5 6.5 8 2l6.5 4.5V14.5h-13Z" fill="none" stroke="#fff" stroke-width="1.3" stroke-linejoin="round"/>
          <path d="M1.5 6.5 8 10.5l6.5-4M1.5 14.5 6.5 9.5M14.5 14.5 9.5 9.5" fill="none" stroke="#fff" stroke-width="1.1"/>
        </svg>
      </li>
    </ul>
  </section>

</main>
</body>
</html>
```